Travel / Surf Shop Brochure

We are running a surf shop and also we are organising surf and multi-sport (bike, longboard, kaiak) trips in summer.
We need a concise well designed brochure to promote our trips (max 4 activities) and also our shop (maybe including few featured products).
We want to keep our production cost low, so a folded brochure would be good start for us.
As an idea you can review our Facebook profile (https://www.facebook.com/tidal.loft), see the photos, etc.
I can provide any photo from there in good resolution.
The surf destination is Portugal, so you can use any blow-mind pic of this destination.
When I'm first looking this brochure I have to think "I NEED IT, I WANT TO GO THERE". The look and feel should be around the the idea of well-being and outdoor entertainment.
The texts will NOT be in english so for the moment you can use some ample or english texts.
Updates
The logo is uploaded.
Please contact me for any requests or questions.
New pictures are uploaded.
Target Market(s)
We are talking with young and mature public, 25-35 years old, active pople.
Industry/Entity Type
Shop
Font styles to use
Look and feel
Each slider illustrates characteristics of the customer's brand and the style your logo design should communicate.

```html
<!DOCTYPE html>
<html lang="en">
<head>
<meta charset="utf-8">
<title>Tidal Loft — Surf Shop Brochure</title>
<link rel="stylesheet" href="https://fonts.googleapis.com/css2?family=Oswald:wght@400;500&family=Open+Sans:wght@400&display=swap">
<style>
  :root {
    --bg: #5f6163;
    --paper: #ffffff;
    --paper-grey: #ecebe8;
    --ink: #1b1b1b;
    --ink-soft: #4a4a4a;
    --sea: #2a9a84;
    --sea-deep: #1c7f70;
    --foam: #f1f3f1;
    --sand: #c9b19b;
    --sand-dark: #8a6f5c;
    --fold: #e2e2e2;
  }
  * { box-sizing: border-box; margin: 0; padding: 0; }
  html, body { width: 1200px; height: 900px; overflow: hidden; }
  body { background: var(--bg); position: relative; font-family: "Open Sans", Arial, sans-serif; }

  .brochure {
    position: absolute; left: 30px; top: 150px;
    width: 1140px; height: 600px;
    display: flex; background: var(--paper);
    overflow: hidden;
  }
  .panel { position: relative; width: 380px; height: 600px; }
  .panel + .panel { border-left: 1px solid var(--fold); }

  /* Cover panel */
  .cover-photo {
    position: absolute; inset: 0;
    background: linear-gradient(to bottom,
      var(--paper-grey) 0%, var(--paper-grey) 16%,
      var(--foam) 24%, #cfe0da 32%,
      var(--sea) 44%, var(--sea-deep) 58%,
      #d8d2c6 68%, var(--sand) 80%, var(--sand-dark) 100%);
  }
  .surfer-ring {
    position: absolute; left: 180px; top: 150px;
    width: 220px; height: 220px; border-radius: 50%;
    border: 2px dotted var(--ink);
  }
  .headline {
    position: absolute; writing-mode: vertical-rl;
    font-family: "Oswald", Arial, sans-serif; font-weight: 400;
    color: var(--ink); letter-spacing: 4px; line-height: 1;
  }
  .headline-join { left: 40px; top: 30px; font-size: 66px; }
  .headline-on { left: 300px; top: 350px; font-size: 86px; font-weight: 500; }

  /* Shop panel */
  .shop-title {
    position: absolute; left: 30px; top: 230px;
    writing-mode: vertical-rl;
    font-family: "Oswald", Arial, sans-serif; font-size: 24px;
    letter-spacing: 2px; color: var(--ink);
  }
  .shop-copy {
    position: absolute; left: 68px; top: 230px; height: 260px;
    writing-mode: vertical-rl;
    font-size: 8px; line-height: 12px; color: var(--ink-soft);
  }
  .shop-copy p { margin-left: 6px; }

  /* Photo circles (positioned within the brochure) */
  .photo-circle {
    position: absolute; border-radius: 50%;
    border: 2px dotted var(--ink);
  }
  .photo-shop {
    left: 545px; top: 150px; width: 270px; height: 270px;
    background: radial-gradient(circle at 40% 45%, #c99a6c 0%, #8a5a3e 40%, #4b3a3a 70%, #2f2e36 100%);
  }
  .photo-sign {
    left: 740px; top: 20px; width: 190px; height: 190px;
    background: linear-gradient(to bottom, #8fc3d0 0%, #b7d7dc 45%, #e9e3dc 60%, #c8312b 75%, #9ab7bc 100%);
  }
  .photo-swim {
    left: 760px; top: 250px; width: 170px; height: 170px;
    background: radial-gradient(circle at 60% 35%, #3a2a3a 0%, #6b3a3e 25%, #c9916f 45%, #d9ab8a 70%, #f2efea 100%);
  }

  .visit {
    position: absolute; left: 200px; top: 440px;
    font-family: "Oswald", Arial, sans-serif; font-size: 17px;
    letter-spacing: 1.5px; color: var(--ink);
  }
</style>
</head>
<body>
  <main class="brochure">
    <section class="panel panel-cover">
      <div class="cover-photo" role="img" aria-label="Surfer carving a turquoise wave above a sandy beach"></div>
      <div class="surfer-ring"></div>
      <h1 class="headline headline-join">JOIN US</h1>
      <p class="headline headline-on">ON</p>
    </section>

    <section class="panel panel-shop">
      <h2 class="shop-title">OUR SHOP</h2>
      <div class="shop-copy">
        <p>Boards, wetsuits and gear for every level.</p>
        <p>Rentals and repairs all season long.</p>
        <p>Open daily from spring to late autumn.</p>
        <p>Find us steps from the beach.</p>
      </div>
    </section>

    <section class="panel panel-visit">
      <p class="visit">COME VISIT US!</p>
    </section>

    <div class="photo-circle photo-shop" role="img" aria-label="Customer browsing colourful clothing inside the shop"></div>
    <div class="photo-circle photo-sign" role="img" aria-label="Red and white shop sign under a blue sky with palm trees"></div>
    <div class="photo-circle photo-swim" role="img" aria-label="Patterned swimwear and a surfboard"></div>
  </main>
</body>
</html>
```